Business Card for Fashion House

We need a business card design for our personalize fashion service for our customers. the business card should reflect reliability, luxury and creativity.
The brand Gravetto is extracted from "Graceful Velvetto"; Gravetto provides fashion designs sprinkled with luxury and style tailored for our elite clients character profile.
Gravetto is created for those who embody class and elegance with a passion for style.
Target Market(s)
Affluent Customers
Industry/Entity Type
Fashion
Contact Information for Business Card
Samira Haddadin
Fashion Designer
Telephone: +971 4 555 0192
Mobile +971 50 555 0147
Emal info@gravetto-example.com
Website www.gravetto-example.com
Social Media Youtube g+ Facebook Instagram Pin /gravetto
Font styles to use
Other font styles liked:
- Audrey provided
Look and feel
Each slider illustrates characteristics of the customer's brand and the style your logo design should communicate.

```html
<!DOCTYPE html>
<html lang="en">
<head>
<meta charset="utf-8">
<title>Gravetto Business Card</title>
<link rel="stylesheet" href="https://fonts.googleapis.com/css2?family=Marcellus&family=Cormorant+Garamond:ital,wght@1,500&display=swap">
<style>
  :root {
    --backdrop: #151515;
    --card-black: #0b0b0b;
    --card-sheen: #2a2a2a;
    --band-white: #f4f4f4;
    --ink-dark: #1a1a1a;
    --ink-light: #e9e9e9;
    --ink-muted: #cfcfcf;
  }
  * { box-sizing: border-box; margin: 0; padding: 0; }
  html, body {
    width: 1200px; height: 864px; overflow: hidden;
    background: var(--backdrop);
    font-family: "Marcellus", "Optima", serif;
  }
  .stage {
    position: relative; width: 1200px; height: 864px;
    display: flex; align-items: center; justify-content: center; gap: 40px;
  }
  .card {
    position: relative; width: 540px; height: 309px; overflow: hidden;
    background: linear-gradient(160deg, var(--card-sheen) 0%, var(--card-black) 45%, #050505 100%);
    box-shadow: 0 10px 30px rgba(0,0,0,0.6);
  }

  /* front */
  .brand {
    position: absolute; top: 26px; left: 0; right: 0;
    display: flex; flex-direction: column; align-items: center; gap: 10px;
  }
  .brand-dot {
    width: 30px; height: 30px; border-radius: 50%;
    border: 2px solid var(--ink-light);
  }
  .brand-name {
    color: var(--ink-light); font-size: 17px; letter-spacing: 7px;
  }
  .divider {
    position: absolute; top: 110px; left: 0; right: 0;
    height: 2px; background: var(--band-white);
  }
  .name-band {
    position: absolute; top: 118px; left: 0; right: 0; height: 58px;
    background: linear-gradient(180deg, #ffffff, #dedede);
    display: flex; flex-direction: column; align-items: center; justify-content: center;
  }
  .person-name {
    color: var(--ink-dark); font-size: 15px; letter-spacing: 1px; text-transform: uppercase;
  }
  .person-title {
    font-family: "Cormorant Garamond", serif; font-style: italic; font-weight: 500;
    color: var(--ink-dark); font-size: 13px; letter-spacing: 0.5px;
  }
  .contact-list {
    position: absolute; top: 196px; left: 178px;
    list-style: none; display: flex; flex-direction: column; gap: 7px;
  }
  .contact-item {
    display: flex; align-items: center; gap: 9px;
    color: var(--ink-muted); font-size: 12px; letter-spacing: 0.8px;
  }
  .contact-icon { width: 12px; height: 12px; flex: none; }

  /* back */
  .card-back svg { position: absolute; inset: 0; }
  .back-brand {
    font-family: "Marcellus", "Optima", serif; font-size: 20px; letter-spacing: 9px;
    fill: var(--ink-dark);
  }
</style>
</head>
<body>
<main class="stage">
  <section class="card card-front" aria-label="Business card front">
    <div class="brand">
      <span class="brand-dot"></span>
      <span class="brand-name">GRAVETTO</span>
    </div>
    <div class="divider"></div>
    <div class="name-band">
      <p class="person-name">Samira Haddadin</p>
      <p class="person-title">Fashion Designer</p>
    </div>
    <ul class="contact-list">
      <li class="contact-item">
        <svg class="contact-icon" viewBox="0 0 12 12"><circle cx="6" cy="6" r="5.4" fill="none" stroke="#cfcfcf"/><path d="M3.4 4.6c.6 1.7 1.9 3 3.9 3.9l.9-.9-1-.8-.6.5c-.8-.4-1.4-1-1.9-1.9l.5-.6-.8-1z" fill="#cfcfcf"/></svg>
        +971 4 555 0192
      </li>
      <li class="contact-item">
        <svg class="contact-icon" viewBox="0 0 12 12"><circle cx="6" cy="6" r="5.4" fill="none" stroke="#cfcfcf"/><rect x="4.2" y="2.8" width="3.6" height="6.4" rx=".6" fill="none" stroke="#cfcfcf" stroke-width=".9"/></svg>
        +971 50 555 0147
      </li>
      <li class="contact-item">
        <svg class="contact-icon" viewBox="0 0 12 12"><circle cx="6" cy="6" r="5.4" fill="none" stroke="#cfcfcf"/><rect x="3" y="4" width="6" height="4.2" fill="none" stroke="#cfcfcf" stroke-width=".8"/><path d="M3 4l3 2.3L9 4" fill="none" stroke="#cfcfcf" stroke-width=".8"/></svg>
        info@gravetto-example.com
      </li>
      <li class="contact-item">
        <svg class="contact-icon" viewBox="0 0 12 12"><circle cx="6" cy="6" r="5.4" fill="none" stroke="#cfcfcf"/><ellipse cx="6" cy="6" rx="2.2" ry="5.2" fill="none" stroke="#cfcfcf" stroke-width=".7"/><path d="M.8 6h10.4M1.6 3.6h8.8M1.6 8.4h8.8" stroke="#cfcfcf" stroke-width=".7"/></svg>
        www.gravetto-example.com
      </li>
    </ul>
  </section>

  <section class="card card-back" aria-label="Business card back">
    <svg viewBox="0 0 540 309" width="540" height="309">
      <defs>
        <linearGradient id="band-fill" x1="0" y1="0" x2="1" y2="1">
          <stop offset="0" stop-color="#ffffff"/>
          <stop offset="1" stop-color="#d9d9d9"/>
        </linearGradient>
      </defs>
      <polygon class="diagonal-band" points="0,95 540,240 540,309 0,165" fill="url(#band-fill)"/>
      <g transform="rotate(15 270 200)">
        <circle cx="270" cy="146" r="15" fill="none" stroke="#e9e9e9" stroke-width="2"/>
        <text class="back-brand" x="274" y="210" text-anchor="middle">GRAVETTO</text>
      </g>
    </svg>
  </section>
</main>
</body>
</html>
```